Coral Bay Pools New website

I currently operate a swimming pool service and repair business and looking for a re design for my website as it has been over 5 years since it was designed. current site is coralbaypoolslv.com

```html
<!DOCTYPE html>
<html lang="en">
<head>
<meta charset="utf-8">
<title>Coral Bay Pools</title>
<link rel="stylesheet" href="https://fonts.googleapis.com/css2?family=Libre+Baskerville:wght@400;700&family=Parisienne&family=Poppins:wght@400;500;600&display=swap">
<style>
:root{
  --blue:#17599a;
  --blue-dark:#114a82;
  --orange:#d08528;
  --text:#333;
  --muted:#555;
  --line:#e3e3e3;
  --white:#fff;
}
*{box-sizing:border-box;margin:0;padding:0}
html,body{width:1200px;height:4666px;overflow:hidden;background:var(--white)}
body{font-family:"Poppins",sans-serif;color:var(--text)}
.page{position:relative;width:1200px;height:4666px;overflow:hidden}
.abs{position:absolute}
.serif{font-family:"Libre Baskerville",serif}
.script{font-family:"Parisienne",cursive;color:var(--orange)}
.btn{position:absolute;display:flex;align-items:center;justify-content:center;font-size:12px;font-weight:600;color:var(--white);background:var(--orange);text-transform:uppercase;border-radius:2px}

/* header */
.brand{position:absolute;display:flex;align-items:center;gap:10px;font-family:"Libre Baskerville",serif;font-weight:700;font-size:22px;color:var(--blue)}
.brand .dot{width:34px;height:34px;border-radius:50%;background:var(--orange)}
.nav{position:absolute;left:355px;top:48px;display:flex;gap:32px;font-size:13px;color:#222}
.nav .active{color:var(--blue);font-weight:500}
.nav-cta{position:absolute;left:962px;top:32px;width:173px;height:52px;background:var(--blue);color:var(--white);font-size:13px;font-weight:600;display:flex;align-items:center;justify-content:center;border-radius:2px}

/* hero */
.hero-photo{position:absolute;left:0;top:125px;width:1200px;height:680px;background:linear-gradient(180deg,#b9c7cc 0%,#5d7d63 28%,#3d6b6c 45%,#1f8ea3 62%,#2aa2b6 80%,#1a6f86 100%)}
.hero-circle{position:absolute;left:516px;top:120px;width:622px;height:622px;border-radius:50%;background:rgba(22,88,158,.93);text-align:center;color:var(--white)}
.hero-circle .kicker{position:absolute;top:175px;width:100%;font-size:14px;font-weight:500}
.hero-circle .title{position:absolute;top:205px;width:100%;font-size:58px;font-family:"Libre Baskerville",serif;letter-spacing:1px}
.hero-circle .title-script{position:absolute;top:228px;width:100%;font-family:"Parisienne",cursive;font-size:112px;color:var(--orange);line-height:1}
.hero-circle p{position:absolute;top:362px;left:70px;right:70px;font-size:13px;line-height:24px}
.hero-circle .hero-btn{position:absolute;left:236px;top:442px;width:154px;height:55px;background:var(--white);color:var(--blue);font-size:13px;font-weight:600;display:flex;align-items:center;justify-content:center;border-radius:2px}

/* headings */
.eyebrow{position:absolute;font-family:"Parisienne",cursive;color:var(--orange);font-size:26px;display:flex;align-items:center;gap:12px}
.eyebrow .rule{width:52px;height:2px;background:var(--orange)}
.h2{position:absolute;font-family:"Libre Baskerville",serif;font-weight:700;color:var(--blue);font-size:41px}
.center{left:0;width:1200px;justify-content:center;text-align:center}

/* photo circles */
.ring{position:absolute;border-radius:50%;border:2px solid var(--orange)}
.photo{position:absolute;border-radius:50%}

/* about */
.about-lead{position:absolute;left:642px;top:1086px;width:490px;font-size:20px;font-weight:600;line-height:31px;color:#111}
.about-copy{position:absolute;left:642px;top:1160px;width:488px;font-size:13.6px;line-height:27.3px;text-align:justify;color:var(--muted)}

/* features */
.feature{position:absolute;width:240px;text-align:center}
.feature .dots{position:absolute;left:33px;top:0;width:174px;height:174px;border-radius:50%;border:4px dotted var(--orange)}
.feature .core{position:absolute;left:51px;top:18px;width:138px;height:138px;border-radius:50%;display:flex;align-items:center;justify-content:center}
.feature .label{position:absolute;top:197px;width:100%;font-family:"Libre Baskerville",serif;font-size:19px;line-height:25px;color:#111}
.feature.blue .core{background:var(--blue)}
.feature.orange .core{background:var(--orange)}
.feature.orange .dots{border-color:var(--blue)}

/* services */
.service{position:absolute;top:2076px;width:346px;height:464px;background:var(--white);box-shadow:0 2px 12px rgba(0,0,0,.16);text-align:center}
.service .photo{left:17px;top:18px;width:312px;height:228px}
.service h3{position:absolute;top:272px;width:100%;font-family:"Libre Baskerville",serif;font-size:22px;color:var(--blue);font-weight:700}
.service p{position:absolute;top:306px;left:24px;right:24px;font-size:13px;line-height:27px;color:#333}
.service .btn{left:111px;top:396px;width:124px;height:44px;font-size:11px}

/* testimonials */
.review{position:absolute;top:2918px;width:296px;height:400px;background:var(--white);box-shadow:0 2px 12px rgba(0,0,0,.14);text-align:center}
.review .avatar{position:absolute;left:79px;top:-72px;width:138px;height:138px;border-radius:50%;border:3px solid var(--orange);background:var(--white)}
.review .avatar.blue{border-color:var(--blue)}
.review .avatar span{position:absolute;inset:6px;border-radius:50%}
.review p{position:absolute;top:90px;left:20px;right:20px;font-size:13.5px;line-height:27px;color:#333}
.review h4{position:absolute;top:302px;width:100%;font-family:"Libre Baskerville",serif;font-size:19px;color:var(--blue);font-weight:700;letter-spacing:.5px}
.review .role{position:absolute;top:330px;width:100%;font-size:13px;color:#444}
.review .stars{position:absolute;top:346px;width:100%;font-size:17px;color:#f2b01e;letter-spacing:1px}
.arrow{position:absolute;width:42px;height:42px;border-radius:50%;background:#e4e4e4;display:flex;align-items:center;justify-content:center}

/* contact */
.field{position:absolute;height:51px;border:1px solid var(--line);font-size:14px;color:#aaa;padding:14px 12px}

/* footer */
.footer-title{position:absolute;top:4318px;font-size:23px;font-weight:600;color:var(--white)}
.links{position:absolute;left:477px;top:4390px;list-style:none;color:var(--white);font-size:13.5px}
.links li{height:32.5px;display:flex;align-items:center;gap:16px}
.links li::before{content:"";width:7px;height:7px;border-radius:50%;background:var(--white)}
.c-item{position:absolute;left:792px;display:flex;align-items:center;gap:18px;color:var(--white);font-size:13.5px;line-height:22px}
.c-icon{width:36px;height:36px;border-radius:50%;background:var(--white);display:flex;align-items:center;justify-content:center;flex:none}
.social{position:absolute;top:4478px;width:36px;height:36px;border-radius:50%;background:var(--white)}
.divider{position:absolute;left:72px;top:4588px;width:1063px;height:1px;background:rgba(255,255,255,.35)}
.copyright{position:absolute;top:4610px;width:1200px;text-align:center;color:var(--white);font-size:14px}
</style>
</head>
<body>
<div class="page">

  <!-- Header -->
  <header>
    <div class="brand" style="left:70px;top:44px"><span class="dot"></span>Coral Bay Pools</div>
    <nav class="nav">
      <span class="active">HOME</span><span>ABOUT US</span><span>OUR SERVICES</span><span>FREE ESTIMATE</span><span>TESTIMONIALS</span><span>BLOG</span>
    </nav>
    <div class="nav-cta">CONTACT US</div>
  </header>

  <!-- Hero -->
  <section>
    <div class="hero-photo" role="img" aria-label="Resort swimming pool with loungers, umbrellas and palm trees"></div>
    <div class="hero-circle" style="top:145px">
      <div class="kicker">WELCOME TO</div>
      <div class="title">CORAL BAY</div>
      <div class="title-script" style="top:222px">Pools</div>
      <p>The swimming pool at your facility should be properly maintained to ensure your guests or residents are safe.</p>
      <div class="hero-btn">CONTACT US</div>
    </div>
    <svg class="abs" style="left:0;top:640px" width="1200" height="220" viewBox="0 0 1200 220">
      <path d="M0 110 C 220 40, 420 50, 620 140 C 800 215, 980 200, 1200 140 L1200 220 L0 220Z" fill="#fff"/>
      <path d="M60 100 C 260 20, 440 40, 620 120 C 800 195, 980 175, 1150 140 C 980 200, 800 225, 620 160 C 440 90, 260 50, 60 100Z" fill="var(--orange)"/>
    </svg>
  </section>

  <!-- About -->
  <section>
    <div class="ring" style="left:72px;top:952px;width:496px;height:496px"></div>
    <div class="photo" style="left:93px;top:973px;width:454px;height:454px;background:radial-gradient(circle at 55% 40%,#c99a56 0%,#5a4a34 35%,#2e4a38 60%,#1d7fa6 85%)" role="img" aria-label="Modern villa with lit pool at dusk"></div>
    <div class="eyebrow" style="left:642px;top:984px">Who We Are <span class="rule"></span></div>
    <h2 class="h2" style="left:642px;top:1024px">About Us</h2>
    <p class="about-lead">We are a full service pool company servicing the Las Vegas Valley.</p>
    <p class="about-copy">My name is Daniel and I'm the owner of Coral Bay Pools. I recently started this business in 2016 to provide Las Vegas with excellent, reliable pool service. Just because we are a new company that doesn't mean we lack experience. I've been in the pool industry for seven years and counting and have managed everything from your backyard pool to olympic sized pools with five plus years managing casino properties as well.</p>
    <div class="btn" style="left:642px;top:1366px;width:138px;height:50px">Read More</div>
  </section>

  <!-- Features -->
  <section>
    <div class="feature blue" style="left:88px;top:1543px">
      <div class="dots"></div>
      <div class="core"><svg width="64" height="64" viewBox="0 0 64 64" fill="none" stroke="#fff" stroke-width="2.4"><circle cx="36" cy="20" r="11"/><path d="M31 20l4 4 7-8"/><path d="M6 44h10l10 6h14c3 0 3-5 0-5h-9"/><path d="M16 44c6-5 12-5 18-2l16-6c3-1 5 3 2 5L38 52"/></svg></div>
      <div class="label">Quality Well<br>Results</div>
    </div>
    <div class="feature orange" style="left:352px;top:1543px">
      <div class="dots"></div>
      <div class="core"><svg width="64" height="64" viewBox="0 0 64 64" fill="none" stroke="#fff" stroke-width="2.4"><circle cx="30" cy="18" r="10"/><path d="M12 56c0-12 8-20 18-20s18 8 18 20"/><circle cx="44" cy="46" r="7"/><path d="M41 46l2 2 4-4"/></svg></div>
      <div class="label">Professional &amp;<br>Trusted Staff</div>
    </div>
    <div class="feature blue" style="left:618px;top:1543px">
      <div class="dots"></div>
      <div class="core"><svg width="64" height="64" viewBox="0 0 64 64" fill="none" stroke="#fff" stroke-width="2.4"><path d="M32 6l5 6 8-2 2 8 8 3-3 8 4 7-7 4 0 8-8-1-5 6-6-5-8 2-2-8-8-3 3-8-4-7 7-4 0-8 8 1z"/><circle cx="32" cy="32" r="12"/><path d="M26 32l4 4 8-8"/></svg></div>
      <div class="label">Committed To<br>Success</div>
    </div>
    <div class="feature orange" style="left:884px;top:1543px">
      <div class="dots"></div>
      <div class="core"><svg width="64" height="64" viewBox="0 0 64 64" fill="none" stroke="#fff" stroke-width="2.2"><path d="M14 10l2 4 4 1-3 3 1 4-4-2-4 2 1-4-3-3 4-1z"/><path d="M32 8l2 4 4 1-3 3 1 4-4-2-4 2 1-4-3-3 4-1z"/><path d="M50 10l2 4 4 1-3 3 1 4-4-2-4 2 1-4-3-3 4-1z"/><circle cx="32" cy="36" r="6"/><circle cx="16" cy="40" r="5"/><circle cx="48" cy="40" r="5"/><path d="M20 56c0-7 5-12 12-12s12 5 12 12"/><path d="M6 56c0-5 4-9 10-9M58 56c0-5-4-9-10-9"/></svg></div>
      <div class="label">100% Clients<br>Satisfied</div>
    </div>
  </section>

  <!-- Services -->
  <section>
    <div class="eyebrow center" style="top:1934px"><span class="rule"></span>What We Do<span class="rule"></span></div>
    <h2 class="h2" style="left:0;width:1200px;text-align:center;top:1974px">Our Services</h2>

    <article class="service" style="left:67px">
      <div class="photo" style="background:radial-gradient(circle at 50% 50%,#6fd0f2,#1d8fd0 70%,#0f6fb0)" role="img" aria-label="Pool skimmer net in clear blue water"></div>
      <h3>POOL SERVICES</h3>
      <p>When you invested in your pool, you knew it was a long-term investment in both money and time. At home, it's an oasis,...</p>
      <div class="btn">Read More</div>
    </article>
    <article class="service" style="left:440px">
      <div class="photo" style="background:linear-gradient(180deg,#b8c0c6 0%,#7b8791 45%,#3f6a7c 70%,#2f7f95 100%)" role="img" aria-label="Rooftop pool overlooking city skyscrapers"></div>
      <h3>COMMERCIAL POOLS</h3>
      <p>As a commercial property owner or manager, doing your job well requires you to be mindful of all the details. ..</p>
      <div class="btn">Read More</div>
    </article>
    <article class="service" style="left:789px">
      <div class="photo" style="background:linear-gradient(180deg,#d9e1e4 0%,#8aa07a 35%,#4fb4c4 65%,#8dd3dc 100%)" role="img" aria-label="Residential lap pool beside a modern house"></div>
      <h3>RESIDENTIAL POOLS</h3>
      <p>Here in Southern Nevada, you know it can get really, really hot. That's why you invested in your pool at home;...</p>
      <div class="btn">Read More</div>
    </article>
  </section>

  <!-- Testimonials -->
  <section>
    <div class="eyebrow center" style="top:2676px"><span class="rule"></span>Client Review<span class="rule"></span></div>
    <h2 class="h2" style="left:0;width:1200px;text-align:center;top:2716px">Our Testimonials</h2>

    <div class="arrow" style="left:70px;top:3062px"><svg width="18" height="10" viewBox="0 0 18 10" fill="none" stroke="#333" stroke-width="1.5"><path d="M17 5H2M6 1L2 5l4 4"/></svg></div>
    <div class="arrow" style="left:1094px;top:3062px"><svg width="18" height="10" viewBox="0 0 18 10" fill="none" stroke="#333" stroke-width="1.5"><path d="M1 5h15M12 1l4 4-4 4"/></svg></div>

    <article class="review" style="left:136px">
      <div class="avatar"><span style="background:linear-gradient(180deg,#e7e3df,#c9b8a8)" role="img" aria-label="Client portrait"></span></div>
      <p>Lorem ipsum dolor sit amet, consectetur adipiscing elit, sed do eiusmod tempor incididunt ut labore et dolore magna aliqua. Quis ipsum suspendisse. ultrices gravida. Risus commodo viverra maecenas accumsan lacus vel facilisis.</p>
      <h4>JONAH MERCER</h4><div class="role">Lorem Ipsum</div><div class="stars">★★★★★</div>
    </article>
    <article class="review" style="left:452px">
      <div class="avatar blue"><span style="background:linear-gradient(180deg,#eef0f2,#4a5566)" role="img" aria-label="Client portrait"></span></div>
      <p>Lorem ipsum dolor sit amet, consectetur adipiscing elit, sed do eiusmod tempor incididunt ut labore et dolore magna aliqua. Quis ipsum suspendisse. ultrices gravida. Risus commodo viverra maecenas accumsan lacus vel facilisis.</p>
      <h4>STEFAN LOWRY</h4><div class="role">Lorem Ipsum</div><div class="stars">★★★★★</div>
    </article>
    <article class="review" style="left:769px">
      <div class="avatar"><span style="background:linear-gradient(180deg,#e9e6e2,#3a3330)" role="img" aria-label="Client portrait"></span></div>
      <p>Lorem ipsum dolor sit amet, consectetur adipiscing elit, sed do eiusmod tempor incididunt ut labore et dolore magna aliqua. Quis ipsum suspendisse. ultrices gravida. Risus commodo viverra maecenas accumsan lacus vel facilisis.</p>
      <h4>AIDEN SHAW</h4><div class="role">Lorem Ipsum</div><div class="stars">★★★★★</div>
    </article>
  </section>

  <!-- Contact -->
  <section>
    <div class="eyebrow" style="left:70px;top:3494px">Get In Touch <span class="rule"></span></div>
    <h2 class="h2" style="left:70px;top:3534px">Contact Us</h2>
    <p class="abs" style="left:72px;top:3607px;font-size:13.5px;color:#333">For more information,Please fill out the following and we will be in touch shortly</p>
    <div class="field" style="left:72px;top:3660px;width:261px">First Name</div>
    <div class="field" style="left:357px;top:3660px;width:260px">Second Name</div>
    <div class="field" style="left:72px;top:3740px;width:261px">Phone</div>
    <div class="field" style="left:357px;top:3740px;width:260px">Subject</div>
    <div class="field" style="left:72px;top:3814px;width:545px;height:100px;padding-top:34px">Message</div>
    <div class="btn" style="left:72px;top:3946px;width:176px;height:42px;font-size:11px">Submit A Message</div>

    <div class="ring" style="left:672px;top:3530px;width:452px;height:452px"></div>
    <div class="photo" style="left:692px;top:3550px;width:412px;height:412px;background:linear-gradient(180deg,#4e5d7a 0%,#6e7a94 35%,#2b2e38 60%,#a8763c 75%,#1d2430 100%)" role="img" aria-label="Beach resort with palm trees lit at dusk"></div>
  </section>

  <!-- Footer -->
  <footer>
    <svg class="abs" style="left:0;top:4040px" width="1200" height="626" viewBox="0 0 1200 626">
      <path d="M0 100 C 200 140, 420 190, 640 120 C 820 60, 1000 40, 1200 70 L1200 626 L0 626Z" fill="var(--blue)"/>
      <path d="M0 100 C 200 140, 420 190, 640 120 C 820 60, 1000 40, 1200 70 L1200 130 C 1000 90, 820 110, 640 170 C 420 240, 200 190, 0 150Z" fill="#fff"/>
      <path d="M70 150 C 250 195, 440 210, 640 140 C 820 80, 1000 60, 1140 80 C 1000 75, 820 110, 640 165 C 440 230, 250 215, 70 150Z" fill="var(--orange)"/>
    </svg>

    <div class="brand" style="left:72px;top:4358px;color:var(--white)"><span class="dot"></span>Coral Bay Pools</div>
    <div class="social" style="left:120px"></div>
    <div class="social" style="left:169px"></div>
    <div class="social" style="left:216px"></div>

    <div class="footer-title" style="left:475px">LINKS</div>
    <ul class="links">
      <li>About Us</li><li>Our Services</li><li>Our Testimonials</li><li>Our Blog</li><li>Contact US</li>
    </ul>

    <div class="footer-title" style="left:792px">CONTACT</div>
    <div class="c-item" style="top:4392px">
      <span class="c-icon"><svg width="16" height="20" viewBox="0 0 16 20"><path d="M8 0a7 7 0 0 0-7 7c0 5 7 13 7 13s7-8 7-13a7 7 0 0 0-7-7zm0 10a3 3 0 1 1 0-6 3 3 0 0 1 0 6z" fill="var(--blue)"/></svg></span>
      <span>Lorem ipsum,Lorem ipsum.<br>Lorem ipsum</span>
    </div>
    <div class="c-item" style="top:4448px">
      <span class="c-icon"><svg width="18" height="18" viewBox="0 0 24 24"><path d="M6.6 10.8a15 15 0 0 0 6.6 6.6l2.2-2.2c.3-.3.7-.4 1-.2 1.1.4 2.3.6 3.6.6.6 0 1 .4 1 1V20c0 .6-.4 1-1 1A17 17 0 0 1 3 4c0-.6.4-1 1-1h3.5c.6 0 1 .4 1 1 0 1.3.2 2.5.6 3.6.1.3 0 .7-.2 1z" fill="var(--blue)"/></svg></span>
      <span>(702) 555-0142</span>
    </div>
    <div class="c-item" style="top:4504px">
      <span class="c-icon"><svg width="18" height="14" viewBox="0 0 18 14"><rect x="0" y="0" width="18" height="14" rx="2" fill="var(--blue)"/><path d="M1 1l8 6 8-6" fill="none" stroke="#fff" stroke-width="1.5"/></svg></span>
      <span>poolsolutions@coralbaypoolslv.com</span>
    </div>

    <div class="divider"></div>
    <div class="copyright">©2018 Coral Bay Pools - Do not copy. All rights reserved.</div>
  </footer>

</div>
</body>
</html>
```